Stonebridge Building and Projects business cards

A business card with watermark background (construction work)

Company logo attached

Home improvement projects
House renovations
Bathroom and kitchen renovations
House extensions
New builds and granny flats

Director Omar Haddani
(Phone number)
omar@sbpbuilding.com.au
(Instagram logo) sbp_building

```html
<!DOCTYPE html>
<html lang="en">
<head>
<meta charset="utf-8">
<title>Stonebridge Building and Projects – Business Cards</title>
<link rel="stylesheet" href="https://fonts.googleapis.com/css2?family=Montserrat:wght@400;500;600&family=Roboto:wght@400&display=swap">
<style>
  :root {
    --brand-blue: #2f77b9;
    --back-blue: #3578b6;
    --ink: #454545;
    --paper: #ffffff;
    --stage: #e9eaec;
  }
  * { margin: 0; padding: 0; box-sizing: border-box; }
  html, body { width: 1200px; height: 1200px; overflow: hidden; background: var(--stage); }
  .sheet { position: relative; width: 1200px; height: 1200px; }

  .card {
    position: absolute;
    left: 170px;
    width: 800px;
    height: 457px;
    transform: scale(1.075);
    transform-origin: top left;
    overflow: hidden;
    font-family: "Montserrat", sans-serif;
  }
  .card--front { top: 59px; background: var(--paper); }
  .card--back { top: 650px; background: var(--back-blue); font-family: "Roboto", sans-serif; }

  /* Front */
  .company-mark {
    position: absolute;
    left: 512px; top: 96px; width: 250px;
    display: flex; align-items: center; gap: 10px;
    color: var(--brand-blue);
    font-weight: 500; font-size: 22px; line-height: 1.2;
  }
  .company-mark__square { width: 14px; height: 14px; background: var(--brand-blue); flex: none; }

  .person { position: absolute; left: 54px; top: 208px; color: var(--ink); }
  .person__name { font-size: 26px; font-weight: 500; letter-spacing: 0.5px; text-transform: uppercase; line-height: 1; }
  .person__name .initial { color: var(--brand-blue); }
  .person__role { margin-top: 8px; font-size: 18px; font-weight: 500; letter-spacing: 0.3px; }

  .contacts { position: absolute; left: 54px; top: 284px; list-style: none; color: var(--ink); font-size: 17.5px; }
  .contacts li { display: flex; align-items: center; gap: 9px; height: 22.5px; }
  .contacts svg { width: 15px; height: 15px; flex: none; }

  .web-band {
    position: absolute; left: 53px; top: 384px; width: 747px; height: 37px;
    background: var(--brand-blue);
  }
  .web-band__icon { position: absolute; left: 8px; top: 7px; width: 23px; height: 23px; }
  .web-band__url {
    position: absolute; right: 52px; top: 8px;
    color: #fff; font-weight: 600; font-size: 17.5px; letter-spacing: 0.3px;
  }

  /* Back */
  .back-mark {
    position: absolute; left: 0; right: 0; top: 170px;
    display: flex; align-items: center; justify-content: center; gap: 18px;
    color: #fff; font-family: "Montserrat", sans-serif; font-weight: 500;
    font-size: 42px; line-height: 1.15; text-align: left;
  }
  .back-mark__square { width: 26px; height: 26px; background: #fff; flex: none; }

  .services {
    position: absolute; left: 0; right: 0; top: 369px;
    color: #fff; font-size: 18px; text-align: center; line-height: 22px;
  }
  .services__row { display: flex; justify-content: center; align-items: center; gap: 12px; }
  .sep { display: inline-grid; grid-template-columns: 3px 3px; gap: 2px; }
  .sep i { width: 3px; height: 3px; background: #fff; display: block; }
</style>
</head>
<body>
<div class="sheet">

  <section class="card card--front">
    <div class="company-mark">
      <span class="company-mark__square"></span>
      <span>Stonebridge Building and Projects</span>
    </div>

    <div class="person">
      <h1 class="person__name"><span class="initial">O</span>mar Haddani</h1>
      <p class="person__role">Director</p>
    </div>

    <ul class="contacts">
      <li>
        <svg viewBox="0 0 24 24"><path fill="#2f77b9" d="M6.6 10.8a15.1 15.1 0 0 0 6.6 6.6l2.2-2.2a1 1 0 0 1 1-.25 11.4 11.4 0 0 0 3.6.57 1 1 0 0 1 1 1V20a1 1 0 0 1-1 1A17 17 0 0 1 3 4a1 1 0 0 1 1-1h3.5a1 1 0 0 1 1 1c0 1.25.2 2.45.57 3.57a1 1 0 0 1-.25 1z"/></svg>
        402-318-7750
      </li>
      <li>
        <svg viewBox="0 0 24 24"><rect x="2" y="5" width="20" height="14" rx="1.5" fill="#2f77b9"/><path d="M3 6.5l9 6.5 9-6.5" fill="none" stroke="#fff" stroke-width="1.6"/></svg>
        omar@sbpbuilding.com.au
      </li>
      <li>
        <svg viewBox="0 0 24 24"><circle cx="12" cy="12" r="10" fill="#2f77b9"/></svg>
        sbp_building
      </li>
    </ul>

    <div class="web-band">
      <svg class="web-band__icon" viewBox="0 0 23 23"><g fill="#fff"><rect x="0" y="0" width="10.5" height="10.5"/><rect x="12.5" y="0" width="10.5" height="10.5"/><rect x="0" y="12.5" width="10.5" height="10.5"/><rect x="12.5" y="12.5" width="10.5" height="10.5"/></g></svg>
      <span class="web-band__url">www.sbpbuilding.com.au</span>
    </div>
  </section>

  <section class="card card--back">
    <div class="back-mark">
      <span class="back-mark__square"></span>
      <span>Stonebridge<br>Building and Projects</span>
    </div>

    <div class="services">
      <p class="services__row">
        <span>Home improvement projects</span>
        <span class="sep"><i></i><i></i><i></i><i></i></span>
        <span>House renovations</span>
        <span class="sep"><i></i><i></i><i></i><i></i></span>
        <span>House extensions</span>
      </p>
      <p class="services__row">
        <span>Bathroom &amp; kitchen renovations</span>
        <span class="sep"><i></i><i></i><i></i><i></i></span>
        <span>New builds &amp; granny flats</span>
      </p>
    </div>
  </section>

</div>
</body>
</html>
```